We need a wordpress design that will incorporate a professional color scheme with company logo in a clean layout. The design needs to consider that this will be developed on a responsive theme. Colors are blue and green of the logo and and an accent color (perhaps very light brown/tan). Client wants a 'modern' look.

Industry/Entity Type

It Company

Font styles to use
Serif
Sans Serif

Colors

Designer to choose colors to be used in the design.

Requirements
Must have
• navigation: 1) Home; 2) Services; 3) Auctions by Type; 4) About Us; 5) QVT Bulletin 6) Videos; 7) Contact Us

VERY general idea of layout is attached, Site will have slideshow, image is attached. Widgets used to are: 1) Email Contact Form; 2) social media icons, QT Linkora, ViewNest; 3) Featured Auctions; 4) News & Events blog; Featured Video

Footer will have affiliation logos, contact info and perhaps smaller company logo:
Phone: (512) 555-0147 / Mobile: (512) 555-0183 (Miriam)
Email: mdorrance482@mailbox-example.com / holden@parkelldorrance.example
Address: 417 FM 1382N • #B208 • PMB315 • Austin, TX 78791

Nice to have
• Use of a dropdown menu

```html
<!DOCTYPE html>
<html lang="en">
<head>
<meta charset="utf-8">
<title>Parkell-Dorrance Auction Marketing</title>
<link href="https://fonts.googleapis.com/css2?family=PT+Sans:wght@400;700&family=Arimo:wght@400;700&display=swap" rel="stylesheet">
<style>
:root{
  --blue:#0d4fa0;
  --blue-dark:#0b3f86;
  --green:#0f7a4e;
  --green-body:#0c6b47;
  --tan:#fbf3e1;
  --grey-card:#d9d7d5;
  --ink:#1b1b1b;
  --link:#1a78c2;
  --footer:#232323;
}
*{box-sizing:border-box;margin:0;padding:0}
html,body{width:902px;height:1200px;overflow:hidden}
body{font-family:"Arimo",Arial,sans-serif;color:var(--ink);background:#fff}
.canvas{position:relative;width:902px;height:1200px;overflow:hidden}
.abs{position:absolute}
.header{left:0;top:0;width:902px;height:102px;background:linear-gradient(#fff,#e6e6e6)}
.brand{left:128px;top:22px;color:var(--blue);font-family:"PT Sans",sans-serif;font-weight:700;font-size:19px;line-height:20px;text-align:center;width:160px}
.brand .mark{display:inline-block;width:12px;height:12px;border-radius:50%;background:var(--green);margin-right:5px;vertical-align:1px}
.social{top:63px;display:flex;gap:7px;left:412px;align-items:center;white-space:nowrap}
.social span{font-family:"PT Sans",sans-serif;font-size:10px;color:#35537a;font-weight:700;display:flex;align-items:center;gap:3px}
.social i{display:inline-block;width:14px;height:14px;border-radius:50%;background:#4b6b9a}
.contact{font-size:10px;font-weight:700;display:flex;align-items:center;gap:8px;white-space:nowrap}
.band-top{left:0;top:102px;width:902px;height:4px;background:var(--blue)}
.nav{left:0;top:106px;width:902px;height:35px;background:var(--green)}
.nav ul{list-style:none;position:absolute;left:111px;top:0;display:flex;height:35px}
.nav li{color:#fff;font-family:"PT Sans",sans-serif;font-size:12px;line-height:35px;text-align:center;border-right:1px solid #0b6740;position:relative;white-space:nowrap}
.nav li:last-child{border-right:0}
.caret{position:absolute;left:50%;bottom:-1px;margin-left:-5px;border:5px solid transparent;border-bottom-color:#222}
.slide-band{left:0;top:141px;width:902px;height:297px;background:var(--blue)}
.slide{left:111px;top:156px;width:676px;height:266px;border:1px solid #fff;background:linear-gradient(135deg,#8e9a94,#5d9484 45%,#6f7a75 80%,#a79a6c)}
.caption{left:259px;top:313px;width:479px;height:65px;background:rgba(0,0,0,.55)}
.caption p{position:absolute;left:7px;top:21px;color:#fff;font-family:"PT Sans",sans-serif;font-size:19px;white-space:nowrap}
.btn-learn{position:absolute;left:368px;top:17px;width:110px;height:31px;background:#139055;border-radius:4px;color:#fff;font-family:"PT Sans",sans-serif;font-size:18px;text-align:center;line-height:31px}
.dropdown{left:290px;top:146px;width:114px;height:98px;background:#222;border-radius:3px;padding-top:2px}
.dropdown div{height:23px;line-height:23px;padding-left:12px;color:#fff;font-size:9.5px;font-weight:700;white-space:nowrap;letter-spacing:-.1px}
.dropdown .active{background:var(--blue)}
.body{left:0;top:438px;width:902px;height:647px;background:var(--green-body)}
.card{width:428px;height:195px;left:115px;background:var(--grey-card)}
.card .photo{position:absolute;left:10px;top:13px;width:158px;height:132px;background:linear-gradient(#7ea7d8 0 35%,#e9dccb 35% 80%,#6d8a52 80%)}
.card .intro,.card .meta{position:absolute;left:178px;width:240px;background:var(--tan);border-radius:3px;padding:7px 7px;font-size:9px;line-height:14px}
.card .intro{top:11px;height:64px}
.card .intro b{display:block;font-weight:400;font-size:10px;margin-bottom:3px}
.card .meta{top:88px;height:99px;font-size:8px;line-height:11px}
.card .meta .kind{color:var(--link);font-size:10px;margin-bottom:3px}
.card .meta strong{display:block;margin-top:5px;font-size:9px}
.btn-blue{position:absolute;top:158px;height:20px;background:var(--blue);color:#fff;font-family:"PT Sans",sans-serif;font-size:11px;line-height:20px;display:flex;align-items:center;gap:5px;padding-left:8px}
.btn-bid{position:absolute;left:191px;top:158px;width:165px;height:22px;background:#111;border-radius:3px;color:#fff;font-size:9px;font-weight:700;display:flex;align-items:center;gap:7px;padding-left:12px;white-space:nowrap}
.news{left:115px;top:905px;width:428px;height:155px;background:#e8e6e4;padding:12px 15px}
.news h2{font-family:"PT Sans",sans-serif;font-size:18px;font-weight:400;margin-bottom:10px}
.news li{list-style:none;font-size:8.5px;line-height:20.5px;white-space:nowrap}
.news li::before{content:"›";margin-right:5px}
.signup{left:569px;top:456px;width:218px;height:141px;background:linear-gradient(#333,#050505);color:#fff;padding:7px 16px}
.signup h2{font-family:"PT Sans",sans-serif;font-weight:400;font-size:18px}
.signup p{font-size:8.5px;line-height:12px;margin-top:5px}
.signup .field{margin-top:9px;width:171px;height:25px;background:#fff;border-radius:3px;color:#333;font-size:9.5px;line-height:25px;padding-left:11px}
.signup .go{margin-top:13px;margin-left:2px;width:103px;height:25px;background:var(--blue);color:#fff;font-size:12px;text-align:center;line-height:25px;border-radius:2px}
.side-h{left:569px;color:#fff;font-family:"PT Sans",sans-serif;font-size:18px}
.feat{left:569px;top:653px;width:218px;height:178px;background:#f3f2f1;padding:9px 8px;font-size:8.5px}
.feat .title{font-weight:700;font-size:9px;padding-left:4px}
.feat .photo{margin-top:6px;height:83px;background:linear-gradient(#b9d4ee 0 30%,#8d3b2b 30% 78%,#5d8b40 78%)}
.feat .date{margin-top:8px;padding-left:4px;line-height:12px;color:#333}
.feat .date b{color:#222}
.feat .sub{margin-top:6px;padding-left:3px;font-size:9px}
.video{left:571px;top:883px;width:217px;height:146px;background:linear-gradient(#e3e7ec 0 30%,#9a9891 30% 70%,#6e8d52 70%)}
.video .bar{position:absolute;left:0;bottom:0;width:217px;height:14px;background:#111;display:flex;align-items:center;gap:6px;padding:0 6px;color:#bbb;font-size:7px}
.video .track{width:80px;height:3px;background:#555}
.footer{left:0;top:1085px;width:902px;height:115px;background:var(--footer)}
.footer .info{position:absolute;left:118px;top:20px;color:#fff;font-size:9.5px;line-height:15.3px;white-space:nowrap}
.footer .brand2{position:absolute;left:525px;top:32px;width:115px;color:#fff;font-family:"PT Sans",sans-serif;font-weight:700;font-size:13px;line-height:14px;text-align:center}
.badge{position:absolute;background:#d8d8d8}
</style>
</head>
<body>
<div class="canvas">
  <header class="header abs">
    <div class="brand abs"><span class="mark"></span>Parkell-Dorrance<br>Auction Marketing</div>
    <div class="social abs">
      <span><i></i>QT</span><span><i style="background:#c33"></i>ViewNest</span><span><i style="background:#2a6fa8"></i>Linkora</span>
    </div>
    <div class="contact abs" style="left:584px;top:35px">
      <svg width="20" height="20" viewBox="0 0 20 20"><circle cx="10" cy="10" r="9" fill="none" stroke="#17854f" stroke-width="2"/><path d="M7 5l2 2-1 2 3 3 2-1 2 2-2 2c-4 0-8-4-8-8z" fill="#17854f"/></svg>
      <span>(512) 555-0147, (512) 555-0183</span>
    </div>
    <div class="contact abs" style="left:592px;top:67px">
      <svg width="26" height="14" viewBox="0 0 26 14"><rect x="6" y="1" width="19" height="12" fill="#17854f"/><path d="M6 1l9.5 7 9.5-7" fill="none" stroke="#fff" stroke-width="1.2"/><path d="M0 4h4M1 7h3M2 10h2" stroke="#17854f"/></svg>
      <span>mdorrance482@mailbox-example.com</span>
    </div>
  </header>
  <div class="band-top abs"></div>
  <nav class="nav abs">
    <ul>
      <li style="width:75px">HOME</li>
      <li style="width:91px">SERVICES</li>
      <li style="width:127px">AUCTIONS BY TYPE<span class="caret"></span></li>
      <li style="width:96px">ABOUT US</li>
      <li style="width:113px">QVT BULLETIN</li>
      <li style="width:82px">VIDEOS</li>
      <li style="width:91px">CONTACT US</li>
    </ul>
  </nav>
  <div class="slide-band abs"></div>
  <div class="slide abs" role="img" aria-label="Slideshow photo of an industrial machine shop floor with green lathes and equipment"></div>
  <div class="caption abs"><p>Making "SOLD" Our Specialty for 30 Years</p><div class="btn-learn">Learn More</div></div>
  <div class="dropdown abs">
    <div>Real Estate</div><div class="active">Business Liquiations</div><div>Commercial</div><div>Appraisal</div>
  </div>

  <main class="body abs"></main>

  <section class="card abs" style="top:456px">
    <div class="photo" role="img" aria-label="Photo of a two-storey stucco house with red shutters"></div>
    <div class="intro"><b>Auction 1</b>Lorem Ipsum is simply dummy text of the printing and typesetting industry.</div>
    <div class="meta"><div class="kind">Online Bidding Only</div>Began:&nbsp; Friday, May 24, 2013 at 10:06 AM EDT<strong>Location</strong>2273 Marlow Ln. NW Cedar Rapids, IA 52499</div>
    <div class="btn-blue" style="left:10px;width:68px"><svg width="10" height="10"><circle cx="5" cy="5" r="4" fill="#fff"/></svg>Details</div>
    <div class="btn-blue" style="left:94px;width:74px"><svg width="13" height="10"><rect x="0" y="0" width="9" height="7" fill="none" stroke="#fff"/><rect x="3" y="3" width="9" height="7" fill="#fff"/></svg>Gallery</div>
    <div class="btn-bid"><svg width="12" height="11"><rect x="0.5" y="0.5" width="11" height="7" fill="none" stroke="#fff"/><path d="M4 10h4M6 8v2" stroke="#fff"/></svg>Click here for Online Bidding</div>
  </section>

  <section class="card abs" style="top:679px">
    <div class="photo" role="img" aria-label="Photo of a two-storey stucco house with red shutters"></div>
    <div class="intro"><b>Auction 1</b>Lorem Ipsum is simply dummy text of the printing and typesetting industry.</div>
    <div class="meta"><div class="kind">Online Bidding Only</div>Began:&nbsp; Friday, May 24, 2013 at 10:06 AM EDT<strong>Location</strong>2273 Marlow Ln. NW Cedar Rapids, IA 52499</div>
    <div class="btn-blue" style="left:10px;width:68px"><svg width="10" height="10"><circle cx="5" cy="5" r="4" fill="#fff"/></svg>Details</div>
    <div class="btn-blue" style="left:94px;width:74px"><svg width="13" height="10"><rect x="0" y="0" width="9" height="7" fill="none" stroke="#fff"/><rect x="3" y="3" width="9" height="7" fill="#fff"/></svg>Gallery</div>
    <div class="btn-bid"><svg width="12" height="11"><rect x="0.5" y="0.5" width="11" height="7" fill="none" stroke="#fff"/><path d="M4 10h4M6 8v2" stroke="#fff"/></svg>Click here for Online Bidding</div>
  </section>

  <section class="news abs">
    <h2>News &amp; Events Blog</h2>
    <ul>
      <li>Great Land Auction Companies Make All the difference Great OK Farms for Sale</li>
      <li>Great Land Auction Companies Make All the difference Great OK Farms for Sale</li>
      <li>Great Land Auction Companies Make All the difference Great OK Farms for Sale</li>
      <li>Great Land Auction Companies Make All the difference Great OK Farms for Sale</li>
    </ul>
  </section>

  <aside class="signup abs">
    <h2>Email Sign Up</h2>
    <p>Lorem Ipsum is simply dummy text of the printing and typesetting industry.</p>
    <div class="field">Enter your Email Address</div>
    <div class="go">Subscribe</div>
  </aside>

  <h2 class="side-h abs" style="top:624px;font-weight:400">Featured Auction</h2>
  <aside class="feat abs">
    <div class="title">Multi Estate &amp; Consignment Auction</div>
    <div class="photo" role="img" aria-label="Photo of a red brick family house with white windows"></div>
    <div class="date"><b>Start Date/ Time:</b> Saturday, April 13,<br>2013 At 10:00 Am</div>
    <div class="sub">Multi Estate &amp; Consignment Auction</div>
  </aside>

  <h2 class="side-h abs" style="top:853px;font-weight:400">Featured Video</h2>
  <div class="video abs" role="img" aria-label="Video still of a grey house with a white front porch">
    <svg class="abs" style="left:88px;top:56px" width="42" height="42" viewBox="0 0 42 42"><circle cx="21" cy="21" r="20" fill="rgba(0,0,0,.75)"/><path d="M16 12l13 9-13 9z" fill="#fff"/></svg>
    <div class="bar"><span style="color:#fff">▶</span><div class="track"></div><span>00:00 / 04:36</span></div>
  </div>

  <footer class="footer abs">
    <div class="info">
      Phone: (512) 555-0147 / Mobile: (512) 555-0183 (Miriam)<br>
      Email: mdorrance482@mailbox-example.com / holden@parkelldorrance.example<br>
      Address: 417 FM 1382N • #B208 • PMB315 • Austin, TX 78791<br>
      Copyright © 2005 - 2014: Parkell-Dorrance Auction Marketing, Inc.<br>
      All Rights Reserved • Powered by: BidHouseHub.example and AuctionRoster.example
    </div>
    <div class="brand2">Parkell-Dorrance<br>Auction Marketing</div>
    <div class="badge" style="left:668px;top:16px;width:36px;height:36px;border-radius:50%"></div>
    <div class="badge" style="left:722px;top:16px;width:32px;height:34px"></div>
    <div class="badge" style="left:657px;top:57px;width:40px;height:34px;border-radius:4px"></div>
    <div class="badge" style="left:705px;top:60px;width:75px;height:28px"></div>
  </footer>
</div>
</body>
</html>
```